Corvanth Veylor - Advanced Skincare and undetectable Makeup for Men

We are in need of a professional webpage for our company Corvanth Veylor. We help every man feel his best by looking his best. Inspired by the myth of Corvanth, we offer makeup and skincare products along with education upon their use. Our mission is to celebrate masculinity in all of its forms, regardless of age, race, sexual orientation, or assigned gender at birth.

The webpage would serve as our online store, as a place where our clients can learn about our brand, view our "How-to" video tutorials, and get product information. An online blog will also be hosted in order to keep clients up to date with news, updates, media mentions, etc.

The color schemes that we use are mostly Black and Gold, with Red accents. please keep in mind that this is a men's cosmetics line, and therefore should read powerful, sexy, confident and bold - all with a high end look and feel.

Think along the lines of brands like Lem Brisko, QDV, Belluti, etc.

our logo is included in the files attached. images and copy will be added in at a later time; hence, general images that fit the feel and filler text is encouraged.

The products to be sold include:
a face cleanser in a pump dispenser bottle (1 size)
a mask in a round jar container (1 size)
a moisturizer in a pump container 1 size)
a concealer in a click pen with a brush applicator (3 shades)
a liquid liner pen (4 shades)
a contouring palette (2 shade options)
a setting spray (single option)

Target Market(s)

Millennial Men

Industry/Entity Type

Beauty

Number of Pages Required

5+ page

Font styles to use
Serif

Colors
ec1f27
000000
faa54b

Requirements
Must have
• ur essential requirements are:
• 1) a stunning and engaging landing page that truly captures the ideals of sexuality, boldness and confidence.
• 2) an interactive and engaging online store that is easy to update / add product / information to.
• 3) Product pages supporting various toggling images of the product, a shade selection option, ingredient information, usage instructions, pricing, and a link to a "how to video" unique to each individual product.
• 4) dedicated space where all of the tutorials can be organized together
• 5) an organized Blog section, that would include a segment for a Q&A section for us to update as the brand grows, ongoing contests (that would be easily hidden if there are no contests running at the moment) as well as general news and updates segment.
• 6) an "about us" page, where our customers are able to learn about our story, inspirations, humanitarian efforts and philosophies in product contents and purity.
• 7) a contact us page, which would include social media links, contact email and telephone number as well as physical address to be updated upon launch.
• 8) discrete privacy policy, terms of use, and return policy links available at the bottom of every page
Nice to have
• 1) A posting forum where clients could post their looks using our products, or maybe a live stream of our Pictoval account.
• 2) a member sign in page so that we can collect and store customer information for faster check out, keep track of purchases attached to their email address (future loyalty program plans) and maintain an email database for email notifications and the such.

```html
<!DOCTYPE html>
<html lang="en">
<head>
<meta charset="utf-8">
<title>Corvanth Veylor</title>
<link rel="stylesheet" href="https://fonts.googleapis.com/css2?family=Poppins:wght@400;500;600;700&display=swap">
<style>
:root{
  --red:#ec1f27;
  --gold:#faa54b;
  --gold-deep:#f4b223;
  --black:#000;
  --ink:#222;
  --muted:#777;
  --grey-bg:#ececec;
  --line:#e2e2e2;
  --white:#fff;
}
*{box-sizing:border-box;margin:0;padding:0}
html,body{width:1200px;height:4568px;overflow:hidden}
body{font-family:'Poppins',sans-serif;color:var(--ink);background:var(--white);position:relative}
.abs{position:absolute}
svg{display:block}

/* hero */
.hero{position:absolute;left:0;top:0;width:1200px;height:728px;
  background:linear-gradient(160deg,#4a3a35 0%,#2a2220 45%,#5b4a43 75%,#2b2422 100%)}
.topbar{position:absolute;left:0;top:0;width:1200px;height:96px;color:var(--white);font-size:15px}
.topbar .contact{position:absolute;left:108px;top:36px;display:flex;gap:34px;align-items:center}
.topbar .contact span{display:flex;gap:8px;align-items:center}
.brandmark{position:absolute;left:450px;top:24px;width:300px;text-align:center;color:var(--gold);
  font-weight:600;font-size:20px;letter-spacing:4px;text-transform:uppercase}
.brandmark .dot{width:34px;height:34px;border:2px solid var(--gold);margin:0 auto 6px}
.search{position:absolute;left:860px;top:30px;width:230px;height:32px;background:var(--white);display:flex}
.search span{flex:1;font-size:12px;color:#999;padding:7px 10px}
.search b{width:36px;background:var(--red);display:flex;align-items:center;justify-content:center}
.nav{position:absolute;left:100px;top:112px;width:1000px;height:72px;background:var(--red);
  display:flex;align-items:center;padding:0 40px;color:var(--white);font-size:16px;font-weight:500}
.nav a{margin-right:62px;color:inherit;text-decoration:none}
.nav .cart{margin-left:auto;margin-right:0;display:flex;gap:10px;align-items:center}
.hero-copy{position:absolute;left:0;top:400px;width:1200px;text-align:center;color:var(--white)}
.hero-copy .welcome{font-size:20px;font-weight:500}
.hero-copy h1{font-size:34px;font-weight:700;line-height:1.2}
.hero-copy p{font-size:15px;width:520px;margin:8px auto 0;line-height:1.5}
.btn-red{display:inline-block;background:var(--red);color:var(--white);font-size:13px;font-weight:600;
  padding:14px 36px;border-radius:30px;text-transform:uppercase}
.hero-copy .btn-red{margin-top:22px}
.dots{position:absolute;left:570px;top:670px;display:flex;gap:8px}
.dots i{width:14px;height:14px;border-radius:50%;background:rgba(255,255,255,.6)}
.dots i:first-child{background:var(--white);border:3px solid #bbb}

.section-title{position:absolute;left:0;width:1200px;text-align:center;font-size:38px;font-weight:700}
.gold{color:var(--gold-deep)}

/* categories */
.cat{position:absolute;top:992px;height:390px;border:14px solid #e6e6e6;background:var(--white)}
.cat.active{border-color:var(--gold-deep)}
.cat h3{text-align:center;margin-top:50px;font-size:17px;font-weight:500;color:var(--gold-deep)}
.cat h3::after{content:"";display:block;width:110px;height:3px;background:var(--gold-deep);margin:12px auto 0}
.cat .ph{position:absolute;left:10px;right:10px;bottom:20px;height:200px}

/* video */
.video-band{position:absolute;left:0;top:1500px;width:1200px;height:520px;background:var(--red)}
.video-band h2{position:absolute;top:78px;width:1200px;text-align:center;color:var(--white);font-size:38px;font-weight:700}
.video-band p{position:absolute;top:152px;left:200px;width:800px;text-align:center;color:var(--white);font-size:13px;line-height:1.6}
.video{position:absolute;left:100px;top:1768px;width:996px;height:422px;
  background:radial-gradient(circle at 55% 45%,#5a4a44 0%,#2c2420 55%,#15110f 100%)}
.play{position:absolute;left:568px;top:1948px}

/* products */
.tabs{position:absolute;top:2436px;left:220px;display:flex;gap:14px}
.tab{border:2px solid var(--red);border-radius:20px;font-size:13px;padding:6px 24px;color:var(--ink);background:var(--white)}
.tab.on{background:var(--red);color:var(--white);display:flex;gap:8px;align-items:center}
.product{position:absolute;width:480px;height:220px}
.product .ph{position:absolute;left:0;top:20px;width:150px;height:170px}
.product .info{position:absolute;left:160px;top:0;width:280px}
.pname{border:1px solid var(--line);border-radius:16px;font-size:13px;padding:6px 18px;
  box-shadow:0 2px 6px rgba(0,0,0,.08);display:inline-block;width:260px}
.stars{color:var(--gold-deep);font-size:15px;letter-spacing:2px;margin-top:10px}
.price{color:var(--red);font-size:15px;font-weight:500}
.desc{font-size:12px;color:var(--muted);line-height:1.5;margin-top:4px;width:230px}
.acts{display:flex;gap:10px;margin-top:12px}
.acts i{width:34px;height:28px;border:1px solid var(--line);border-radius:14px;display:flex;align-items:center;justify-content:center}
.view-link{position:absolute;display:flex;gap:12px;align-items:center;color:var(--red);font-size:17px;font-weight:500}

/* blog */
.blog-band{position:absolute;left:0;top:3160px;width:1200px;height:740px;background:var(--grey-bg)}
.blog-intro{position:absolute;left:100px;top:3416px;width:420px;font-size:13px;color:#555;line-height:1.6}
.blog-rule{position:absolute;left:100px;top:3536px;width:180px;height:4px;background:var(--gold-deep)}
.post{position:absolute;width:232px;background:var(--white);box-shadow:0 2px 8px rgba(0,0,0,.08)}
.post .ph{height:128px}
.post h4{color:var(--red);font-size:15px;font-weight:600;text-align:center;margin-top:14px}
.post p{font-size:11px;color:var(--muted);text-align:center;padding:4px 18px;line-height:1.5}
.post .meta{display:flex;justify-content:space-between;font-size:11px;color:var(--muted);padding:12px 14px 14px;border-top:1px solid var(--line);margin-top:8px}
.post .meta span{display:flex;gap:6px;align-items:center}

/* footer */
.footer-red{position:absolute;left:0;top:3900px;width:1200px;height:220px;background:var(--red);color:var(--white)}
.fcol{position:absolute;top:44px;width:330px;text-align:center}
.fcol h5{font-size:24px;font-weight:600}
.fcol p{font-size:15px;margin-top:24px;line-height:1.5}
.footer-dark{position:absolute;left:0;top:4120px;width:1200px;height:448px;
  background:linear-gradient(180deg,#0c0a09 0%,#1f1917 55%,#0d0b0a 100%)}
.footer-dark .brandmark{top:96px}
.socials{position:absolute;left:560px;top:310px;display:flex;gap:12px}
.socials i{width:16px;height:16px;border-radius:50%;background:#bbb}
.copy{position:absolute;top:360px;width:1200px;text-align:center;color:#ccc;font-size:13px}
</style>
</head>
<body>

<header class="hero" role="img" aria-label="Photograph of makeup brushes and cosmetic powders on a dark surface">
  <div class="topbar">
    <div class="contact">
      <span><svg width="16" height="16" viewBox="0 0 24 24"><path fill="#ec1f27" d="M6.6 10.8a15 15 0 0 0 6.6 6.6l2.2-2.2c.3-.3.7-.4 1-.2 1.1.4 2.3.6 3.6.6.6 0 1 .4 1 1V20c0 .6-.4 1-1 1A17 17 0 0 1 3 4c0-.6.4-1 1-1h3.5c.6 0 1 .4 1 1 0 1.3.2 2.5.6 3.6.1.3 0 .7-.2 1z"/></svg>+1 555 014 2290</span>
      <span><svg width="16" height="16" viewBox="0 0 24 24"><circle cx="12" cy="8" r="4" fill="#ec1f27"/><path fill="#ec1f27" d="M4 21c0-4.4 3.6-7 8-7s8 2.6 8 7z"/></svg>Login</span>
    </div>
    <div class="brandmark"><div class="dot"></div>Corvanth Veylor</div>
    <div class="search"><span>Search Here...</span><b><svg width="14" height="14" viewBox="0 0 24 24"><circle cx="10" cy="10" r="6" fill="none" stroke="#fff" stroke-width="3"/><path d="M15 15l6 6" stroke="#fff" stroke-width="3"/></svg></b></div>
  </div>
  <nav class="nav">
    <a>Home</a><a>Shop</a><a>Blog</a><a>Products</a><a>About Us</a><a>Contact Us</a>
    <a class="cart"><svg width="20" height="18" viewBox="0 0 24 22"><path fill="#fff" d="M1 1h4l1 4h16l-3 9H8zM8 17a2 2 0 1 0 0 4 2 2 0 0 0 0-4zm10 0a2 2 0 1 0 0 4 2 2 0 0 0 0-4z"/></svg>Cart</a>
  </nav>
  <div class="hero-copy">
    <div class="welcome">Welcome To</div>
    <h1>Corvanth Veylor</h1>
    <p>Lorem ipsum dolor sit amet, consectetur adipiscing elit, sed do eiusmod tempor incididunt ut labore et</p>
    <span class="btn-red">Shop Now</span>
  </div>
  <div class="dots"><i></i><i></i><i></i></div>
</header>

<h2 class="section-title gold" style="top:856px">Popular Categories</h2>
<div class="cat" style="left:120px;width:264px"><h3>Skincare</h3><div class="ph" role="img" aria-label="Skincare products arrangement" style="background:linear-gradient(135deg,#f3d6d2,#c9313a 60%,#2b2b2b)"></div></div>
<div class="cat active" style="left:460px;width:270px"><h3>Cosmetics</h3><div class="ph" role="img" aria-label="Gold cosmetic jars and bottles" style="background:linear-gradient(135deg,#f6ead0,#d4a850 55%,#8a6a2a)"></div></div>
<div class="cat" style="left:800px;width:264px"><h3>Gift Shop</h3><div class="ph" role="img" aria-label="Pink gift bag with makeup items" style="background:linear-gradient(135deg,#f9d7e6,#e6357e 60%,#5a2a3a)"></div></div>

<section class="video-band">
  <h2>Our Video</h2>
  <p>Sed ut perspiciatis unde omnis iste natus error sit voluptatem accusantium doloremque laudantium, totam rem aperiam, eaque ipsa quae ab illo inventore veritatis et quasi architecto beatae vitae dicta sunt explicabo.</p>
</section>
<div class="video" role="img" aria-label="Video still of makeup brushes with scattered powder"></div>
<svg class="play" width="64" height="64" viewBox="0 0 64 64"><circle cx="32" cy="32" r="28" fill="none" stroke="#fff" stroke-width="4"/><path d="M26 20l18 12-18 12z" fill="#fff"/></svg>

<h2 class="section-title" style="top:2328px;color:var(--red)">Show Products</h2>
<div class="tabs">
  <span class="tab on"><svg width="8" height="8"><circle cx="4" cy="4" r="4" fill="#fff"/></svg>Best Sellers</span>
  <span class="tab">Featured</span><span class="tab">Top Review</span><span class="tab">Special</span><span class="tab">New Arrivals</span>
</div>

<div class="product" style="left:100px;top:2580px">
  <div class="ph" role="img" aria-label="Blue face cleanser pump bottle" style="background:radial-gradient(circle,#8fe0ee,#3bb8d3 60%,#fff 95%)"></div>
  <div class="info"><div class="pname">Face Cleanser</div><div class="stars">★★★★★</div><div class="price">$20.00</div>
  <div class="desc">Sed ut perspiciatis unde omnis iste natus error sit</div>
  <div class="acts"><i>⟳</i><i style="color:var(--red)">♥</i><i>👁</i></div></div>
</div>
<div class="product" style="left:640px;top:2580px">
  <div class="ph" role="img" aria-label="White moisturizer jar" style="background:radial-gradient(circle,#fafafa,#d8d8d8 60%,#fff 95%)"></div>
  <div class="info"><div class="pname">Moisturizer</div><div class="stars">★★★★★</div><div class="price">$20.00</div>
  <div class="desc">Sed ut perspiciatis unde omnis iste natus error sit</div>
  <div class="acts"><i>⟳</i><i style="color:var(--red)">♥</i><i>👁</i></div></div>
</div>
<div class="product" style="left:100px;top:2852px">
  <div class="ph" role="img" aria-label="Gold concealer pen" style="background:radial-gradient(circle,#f6d990,#d9a63a 50%,#fff 90%)"></div>
  <div class="info"><div class="pname">Concealer Pen</div><div class="stars">★★★★★</div><div class="price">$20.00</div>
  <div class="desc">Sed ut perspiciatis unde omnis iste natus error sit</div>
  <div class="acts"><i>⟳</i><i style="color:var(--red)">♥</i><i>👁</i></div></div>
</div>
<div class="product" style="left:640px;top:2852px">
  <div class="ph" role="img" aria-label="Black liquid liner pen" style="background:radial-gradient(circle,#666,#1a1a1a 45%,#fff 85%)"></div>
  <div class="info"><div class="pname">Liquid Liner Pen</div><div class="stars">★★★★★</div><div class="price">$20.00</div>
  <div class="desc">Sed ut perspiciatis unde omnis iste natus error sit</div>
  <div class="acts"><i>⟳</i><i style="color:var(--red)">♥</i><i>👁</i></div></div>
</div>
<div class="view-link" style="left:492px;top:3086px">View All Products
  <svg width="22" height="22" viewBox="0 0 22 22"><circle cx="11" cy="11" r="11" fill="#ec1f27"/><path d="M6 11h9M11 7l4 4-4 4" stroke="#fff" stroke-width="2" fill="none"/></svg></div>

<section class="blog-band"></section>
<h2 class="section-title gold" style="top:3288px">Latest Blog</h2>
<p class="blog-intro">Sed ut perspiciatis unde omnis iste natus error sit voluptatem accusantium doloremque laudantium, totam rem aperiam, eaque ipsa quae ab illo inventore veritatis et quasi</p>
<div class="blog-rule"></div>

<article class="post" style="left:100px;top:3600px"><div class="ph" role="img" aria-label="Eyeshadow palettes and brushes" style="background:linear-gradient(135deg,#b4869a,#6a4a5a)"></div>
  <h4>Lorem Ipsum</h4><p>Sed ut perspiciatis unde omnis iste natus error sit</p>
  <div class="meta"><span><svg width="12" height="12" viewBox="0 0 12 12"><rect x="1" y="2" width="10" height="9" fill="none" stroke="#ec1f27"/><path d="M1 5h10" stroke="#ec1f27"/></svg>July, 14 2018</span><span><svg width="14" height="12" viewBox="0 0 14 12"><path d="M1 1h12v7H6l-3 3V8H1z" fill="#ec1f27"/></svg>2</span></div></article>
<article class="post" style="left:360px;top:3600px"><div class="ph" role="img" aria-label="Makeup products on dark table" style="background:linear-gradient(135deg,#3a2e2e,#7a3a44)"></div>
  <h4>Lorem Ipsum</h4><p>Sed ut perspiciatis unde omnis iste natus error sit</p>
  <div class="meta"><span><svg width="12" height="12" viewBox="0 0 12 12"><rect x="1" y="2" width="10" height="9" fill="none" stroke="#ec1f27"/><path d="M1 5h10" stroke="#ec1f27"/></svg>July, 14 2018</span><span><svg width="14" height="12" viewBox="0 0 14 12"><path d="M1 1h12v7H6l-3 3V8H1z" fill="#ec1f27"/></svg>2</span></div></article>
<article class="post" style="left:612px;top:3412px"><div class="ph" role="img" aria-label="Brushes and powder on wooden surface" style="background:linear-gradient(135deg,#c9a890,#6a4e40)"></div>
  <h4>Lorem Ipsum</h4><p>Sed ut perspiciatis unde omnis iste natus error sit</p>
  <div class="meta"><span><svg width="12" height="12" viewBox="0 0 12 12"><rect x="1" y="2" width="10" height="9" fill="none" stroke="#ec1f27"/><path d="M1 5h10" stroke="#ec1f27"/></svg>July, 14 2018</span><span><svg width="14" height="12" viewBox="0 0 14 12"><path d="M1 1h12v7H6l-3 3V8H1z" fill="#ec1f27"/></svg>2</span></div></article>
<article class="post" style="left:868px;top:3412px"><div class="ph" role="img" aria-label="Brush with glowing blue powder burst" style="background:radial-gradient(circle at 50% 55%,#3fd0e8,#0f3a48 55%,#050a0c)"></div>
  <h4>Lorem Ipsum</h4><p>Sed ut perspiciatis unde omnis iste natus error sit</p>
  <div class="meta"><span><svg width="12" height="12" viewBox="0 0 12 12"><rect x="1" y="2" width="10" height="9" fill="none" stroke="#ec1f27"/><path d="M1 5h10" stroke="#ec1f27"/></svg>July, 14 2018</span><span><svg width="14" height="12" viewBox="0 0 14 12"><path d="M1 1h12v7H6l-3 3V8H1z" fill="#ec1f27"/></svg>2</span></div></article>
<div class="view-link" style="left:760px;top:3806px">View All Blog
  <svg width="22" height="22" viewBox="0 0 22 22"><circle cx="11" cy="11" r="11" fill="#ec1f27"/><path d="M6 11h9M11 7l4 4-4 4" stroke="#fff" stroke-width="2" fill="none"/></svg></div>

<footer>
  <div class="footer-red">
    <div class="fcol" style="left:140px"><h5>Address</h5><p>#18, 47 Harrow Lane,<br>Westmere, FL 3021</p></div>
    <div class="fcol" style="left:435px"><h5>Call Now!</h5><p>Tel.: (+1) 555 014 2290</p></div>
    <div class="fcol" style="left:730px"><h5>Info</h5><p>Email: info@corvanthveylor.com</p></div>
  </div>
  <div class="footer-dark" role="img" aria-label="Dark photograph of makeup brushes">
    <div class="brandmark"><div class="dot"></div>Corvanth Veylor</div>
    <div class="socials"><i></i><i></i><i></i><i></i></div>
    <div class="copy">© 2018 Corvanth Veylor | All Rights Reserved</div>
  </div>
</footer>
</body>
</html>
```